Workshop PPT Update for AI Transformation Sessions

Our strategic consulting firm runs strategy workshops using slides as workshop exercises. These slides are used to communicate to the participants in advance, run the workshops and produce the final deliverable.

It is time for a design "upgrade". We'd like them to be more engaging, hipper and more interesting. These slides are utilitarian, so clean and usable is good. I have attached the example of what we have today. I have also attached an example of another company's slides that I like.

We can't rip off their design nor can we go away 100% from what we have. But I think it is possible to "update" our look to something closer to their look. Grey colors are fine with some color pop.

Slide styles needed are - 1) Cover Page, 2) Instructions Page, 3) Bullet list 4) Worksheet (place for participants to add content 5) Table, 6) Two column.

```html
<!DOCTYPE html>
<html lang="en">
<head>
<meta charset="utf-8">
<title>PathAhead Workshop Slide Templates</title>
<link href="https://fonts.googleapis.com/css2?family=Poppins:wght@400;500;600&display=swap" rel="stylesheet">
<style>
:root{
  --slate:#464a59;
  --slate-deep:#3d4150;
  --red:#b0443f;
  --white:#ffffff;
  --line:#d9d9de;
  --ink:#222;
}
*{margin:0;padding:0;box-sizing:border-box}
html,body{width:1200px;height:1067px;overflow:hidden;background:#fff}
body{position:relative;font-family:'Poppins',sans-serif;color:var(--ink)}
.slide{position:absolute;width:570px;height:320px;overflow:hidden;background:var(--white);box-shadow:0 0 3px rgba(0,0,0,.18)}
.s1{left:21px;top:26px;background:var(--slate)}
.s2{left:608px;top:26px}
.s3{left:21px;top:368px}
.s4{left:608px;top:368px}
.s5{left:21px;top:713px}
.s6{left:608px;top:713px}
.side-bar{position:absolute;left:0;top:0;width:37px;height:100%;background:var(--red)}
.side-brand{position:absolute;left:18px;top:75px;transform:translate(-50%,-50%) rotate(-90deg);color:var(--white);font-weight:500;font-size:21px;white-space:nowrap}
.slide-num{position:absolute;left:5px;bottom:8px;width:27px;height:27px;border-radius:50%;background:var(--white);color:var(--red);font-size:11px;font-weight:500;display:flex;align-items:center;justify-content:center}
.dark-panel{position:absolute;left:399px;top:0;right:0;bottom:0;background:var(--slate)}
/* cover */
.cover-brand{position:absolute;left:25px;top:50px;color:var(--white);font-size:38px;font-weight:500;letter-spacing:-.5px}
.cover-title{position:absolute;left:25px;top:112px;color:var(--white);font-size:19px;font-weight:500}
.cover-list{position:absolute;left:25px;top:153px;width:210px;list-style:none;color:var(--white);font-size:10px;line-height:19px}
.cover-list li{position:relative;padding-left:20px}
.cover-list li::before{content:"";position:absolute;left:1px;top:5px;width:7px;height:9px;border:1.6px solid var(--white);border-radius:50%}
.cover-photo{position:absolute;left:264px;top:22px}
/* kickoff */
.scene{position:absolute;left:37px;top:0;right:0;bottom:0;background:linear-gradient(100deg,#cfd0d1 0%,#a9a8a6 40%,#6d6f78 70%,#4d5160 100%)}
.scene-title{position:absolute;right:35px;top:112px;text-align:right;color:var(--white)}
.scene-title h2{font-size:25px;font-weight:500;line-height:1.2}
.scene-title p{font-size:16px;font-weight:500;line-height:29px;margin-top:3px}
/* table */
.slide-heading{color:var(--red);font-weight:500}
.s3 .slide-heading{position:absolute;left:37px;right:0;top:34px;text-align:center;font-size:20px}
.plan-table{position:absolute;left:50px;top:77px;width:497px;border-collapse:separate;border-spacing:2px 0;font-size:6.3px;text-align:center}
.plan-table th{height:28px;color:var(--white);font-size:9.5px;font-weight:500;line-height:1.3;border-radius:2px 2px 0 0}
.plan-table th.dark{background:var(--slate)}
.plan-table th.red{background:var(--red)}
.plan-table td{height:42px;border:1px solid var(--line);border-top:none;vertical-align:middle;color:#333}
.plan-table td.lvl{font-size:7.5px;width:61px}
/* overview */
.step{position:absolute;right:238px;text-align:right;width:320px}
.step h3{color:var(--red);font-size:12.5px;font-weight:500;line-height:16px}
.step p{font-size:7.5px;color:#222;line-height:12px}
.step-num{position:absolute;left:352px;width:30px;height:30px;border-radius:50%;background:var(--red);color:var(--white);font-size:11px;display:flex;align-items:center;justify-content:center}
.step-fade{position:absolute;left:367px;width:32px;height:30px;background:linear-gradient(90deg,rgba(176,68,63,.55),rgba(176,68,63,0))}
.panel-text{position:absolute;right:34px;text-align:right;color:var(--white)}
.panel-text h2{font-size:20px;font-weight:500;line-height:30px}
.panel-text p{font-size:8.5px;line-height:20px}
/* instructions */
.s5 .slide-heading{position:absolute;left:52px;top:15px;font-size:20px}
.purpose{position:absolute;left:50px;top:53px;font-size:8px}
.purpose b{color:var(--red);font-weight:500;font-size:10.5px;margin-right:5px}
.instr-label{position:absolute;left:37px;width:362px;top:78px;text-align:center;color:var(--red);font-size:10px}
.instr-grid{position:absolute;left:40px;top:106px;display:grid;grid-template-columns:repeat(3,115px);grid-template-rows:94px 94px;gap:5px}
.instr-box{background:var(--slate);color:var(--white);font-size:9px;line-height:16px;display:flex;align-items:center;justify-content:center;text-align:center;padding:6px}
.panel-list{position:absolute;right:13px;text-align:right;color:var(--white)}
.panel-list h3{font-size:13px;font-weight:500}
.panel-list p{font-size:8px;line-height:20px}
/* principles */
.principle{position:absolute;width:115px;height:146px;background:var(--white);border:1px solid #e3e3e6;box-shadow:0 1px 3px rgba(0,0,0,.12);text-align:center;padding-top:18px}
.principle h4{color:var(--red);font-size:11.5px;font-weight:500;margin-bottom:10px}
.principle p{font-size:6.3px;line-height:13.4px;padding:0 8px;color:#222}
</style>
</head>
<body>

<section class="slide s1">
  <div class="cover-brand">PathAhead</div>
  <h1 class="cover-title">Getting Started</h1>
  <ul class="cover-list">
    <li>Complete the Engagement Sizing Survey.</li>
    <li>Collect relevant inputs.</li>
    <li>Determine workshop participants &amp; date.</li>
    <li>Send invites, to include pre-work.</li>
  </ul>
  <svg class="cover-photo" width="300" height="290" viewBox="0 0 300 290">
    <defs>
      <linearGradient id="coverPhotoFill" x1="0" y1="0" x2="1" y2="1">
        <stop offset="0" stop-color="#a9845e"/>
        <stop offset=".5" stop-color="#d9d7d2"/>
        <stop offset="1" stop-color="#6f7a6a"/>
      </linearGradient>
    </defs>
    <path d="M20 150 A130 135 0 0 1 240 35" fill="none" stroke="var(--red)" stroke-width="5"/>
    <path d="M270 90 A130 135 0 0 1 160 285" fill="none" stroke="var(--red)" stroke-width="5"/>
    <circle cx="139" cy="137" r="126" fill="url(#coverPhotoFill)" role="img" aria-label="Photo of two colleagues reviewing work on a laptop in front of a chart display"/>
  </svg>
</section>

<section class="slide s2">
  <div class="scene" role="img" aria-label="Photo of a presenter at a whiteboard leading a meeting"></div>
  <div class="side-bar"></div>
  <div class="side-brand">PathAhead</div>
  <div class="slide-num">02</div>
  <div class="scene-title">
    <h2>Kickoff &amp; Discovery</h2>
    <p>Sizing &amp; Scoping AI<br>Transformation</p>
  </div>
</section>

<section class="slide s3">
  <div class="side-bar"></div>
  <div class="side-brand">PathAhead</div>
  <div class="slide-num">03</div>
  <h2 class="slide-heading">Plan Structure</h2>
  <table class="plan-table">
    <tr>
      <th class="dark" colspan="2">Level</th>
      <th class="red">Planning Element &amp;<br>Definition</th>
      <th class="dark">Accountability/Owner<br>Frequency</th>
      <th class="red">Frequency of<br>Modification</th>
    </tr>
    <tr><td class="lvl">1</td><td>What<br>(overall)</td><td>Strategic Priorities</td><td>N/A</td><td>3+ years</td></tr>
    <tr><td class="lvl">1.1</td><td>What<br>(this year)</td><td>Goals<br>Outcomes &amp; Strategies</td><td>Executive Leadership</td><td>1-3 years</td></tr>
    <tr><td class="lvl">1.1.1</td><td rowspan="2">How</td><td>Key Performance Indicators<br>and/or Initiatives</td><td></td><td>1 year<br>(w/ qrtly targets)</td></tr>
    <tr><td class="lvl">1.1.1.1</td><td>Action Items</td><td></td><td>Quarterly/Monthly</td></tr>
  </table>
</section>

<section class="slide s4">
  <div class="side-bar"></div>
  <div class="side-brand">PathAhead</div>
  <div class="slide-num">04</div>
  <div class="dark-panel"></div>

  <div class="step" style="top:10px"><h3>Confirm Company Direction</h3><p>Recap organizational purpose, values, vision &amp; winning strategy.</p></div>
  <div class="step" style="top:68px"><h3>Develop AI Vision</h3></div>
  <div class="step" style="top:116px;width:340px"><h3>Develop AI Guiding Principles</h3><p>Developed AI Guiding Principles, supporting policies to include approved tools.</p></div>
  <div class="step" style="top:167px"><h3>Agree on a Governance Approach</h3><p>Agreed upon governance approach, structure, &amp; executive champion.</p></div>
  <div class="step" style="top:223px"><h3>Agree on a Training &amp; Learning Approach</h3><p>Set approach to training &amp; continuous learning.</p></div>
  <div class="step" style="top:274px"><h3>Determine Rollout &amp; Communication</h3><p>Organizational rollout &amp; continuous communication.</p></div>

  <div class="step-fade" style="top:15px"></div><div class="step-num" style="top:15px">01</div>
  <div class="step-fade" style="top:66px"></div><div class="step-num" style="top:66px">02</div>
  <div class="step-fade" style="top:122px"></div><div class="step-num" style="top:122px">03</div>
  <div class="step-fade" style="top:173px"></div><div class="step-num" style="top:173px">04</div>
  <div class="step-fade" style="top:229px"></div><div class="step-num" style="top:229px">05</div>
  <div class="step-fade" style="top:280px"></div><div class="step-num" style="top:280px">06</div>

  <div class="panel-text" style="top:46px">
    <h2>Workshop<br>Overview</h2>
    <p style="margin-top:4px">Participants: Execs<br>Duration: 2 hrs.<br>Prep Work:</p>
    <p style="margin-top:8px;margin-right:-8px">Org Strategy &nbsp;«<br>2023 Goal Performance &nbsp;«<br>Existing policies &nbsp;«<br>Pre-thinking questions &nbsp;«</p>
  </div>
</section>

<section class="slide s5">
  <div class="side-bar"></div>
  <div class="side-brand">PathAhead</div>
  <div class="slide-num">05</div>
  <div class="dark-panel"></div>
  <h2 class="slide-heading">Creating your AI Guiding Principles</h2>
  <p class="purpose"><b>Purpose:</b>To create behavioral statements that everyone is expected to adhere to.</p>
  <p class="instr-label">Instructions:</p>
  <div class="instr-grid">
    <div class="instr-box">Create the Outline.<br>Determine the topics that need a principle.</div>
    <div class="instr-box">Audit the Outline.<br>Look at the current policies to determine if all topics are covered.</div>
    <div class="instr-box">Draft the Guiding Principles.</div>
    <div class="instr-box">Determine which GPs need detailed policies.</div>
    <div class="instr-box">Determine which AI Tools support the GPs.</div>
    <div class="instr-box">Finalize via a legal and executive review.</div>
  </div>
  <div class="panel-list" style="top:44px">
    <h3>Your Existing Material</h3>
    <p style="margin-top:4px">Company Values &nbsp;«<br>Current Policies (GDPR, &nbsp;«<br>CCPA, etc.) &nbsp;&nbsp;&nbsp;<br>Legal Guidance &nbsp;«<br>OTHER &nbsp;«</p>
  </div>
  <div class="panel-list" style="top:188px">
    <h3>Examples for Inspiration</h3>
    <p style="margin-top:4px">See next slides</p>
    <h3 style="margin-top:8px">PromptPal Prompts</h3>
    <p style="margin-top:4px">HERE</p>
  </div>
</section>

<section class="slide s6">
  <div class="side-bar"></div>
  <div class="side-brand">PathAhead</div>
  <div class="slide-num">06</div>
  <div class="dark-panel"></div>
  <div class="principle" style="left:43px;top:15px"><h4>Principle #1</h4><p>Complete perspective from Executives, Directors, Managers &amp; Staff. Conduct competitive analysis and customer research (optional).</p></div>
  <div class="principle" style="left:161px;top:15px"><h4>Principle #2</h4><p>Complete perspective from Executives, Directors, Managers &amp; Staff. Conduct competitive analysis and customer research (optional).</p></div>
  <div class="principle" style="left:279px;top:15px"><h4>Principle #3</h4><p>Complete perspective from Executives, Directors, Managers &amp; Staff. Conduct competitive analysis and customer research (optional).</p></div>
  <div class="principle" style="left:96px;top:163px"><h4>Principle #4</h4><p>Complete perspective from Executives, Directors, Managers &amp; Staff. Conduct competitive analysis and customer research (optional).</p></div>
  <div class="principle" style="left:214px;top:163px"><h4>Principle #5</h4><p>Complete perspective from Executives, Directors, Managers &amp; Staff. Conduct competitive analysis and customer research (optional).</p></div>
  <div class="panel-text" style="top:80px;right:46px;text-align:center">
    <h2 style="font-size:17px;line-height:29px">AI Guiding<br>Principles</h2>
    <p style="margin-top:8px">What guides our<br>decision-making and<br>approach?</p>
  </div>
</section>

</body>
</html>
```